Sophisticated, clean website reflecting my feminine, playful side to sell my abstract art,

I need a website no more than 3 pages to showcase my paintings, a little about me and some contact info. I do abstracts so looking for something a little edgy, yet feminine and current.
Updates

Hi there, These are some artists websites that I Iike: Marnelvoss.com (I like how airy it is) peterwallombry.com garethpolvens.com (I like how it scrolls) I'll need a place for a photo ( a headshot-i do not have it yet so I'll need to be able to upload that later) as well as an area for my bio. Also, it's important that I will be able to upload any new photos and descriptions easily so it should be user friendly. Lastly, I like in a sunny place so would like to have this seem upbeat and playful as that is how i like to paint. thanks-I'm trying to upload my photos now -

Target Market(s)

ppl ages 35-70 who want large scale art for their homes

Industry/Entity Type

art

Coding

Coded - Design and coding required

Number of Pages Required

3 page

Colors

Designer to choose colors to be used in the design.

Requirements
Must have
• photos of my art, a place for my bio, be easy to reach me. tasteful-nothing too "in your face" -my clients are pretty high end and organized. They like clean lines
Nice to have
• sophisticated background, muted tones in the back-similar clean font throughout-no cursive
Should not have
• too many dark areas. Too many blocks of color. Too serious.

```html
<!DOCTYPE html>
<html lang="en">
<head>
<meta charset="utf-8">
<title>Lorna Velcourt — Abstract Paintings</title>
<link href="https://fonts.googleapis.com/css2?family=Quicksand:wght@300;400;500&display=swap" rel="stylesheet">
<style>
  :root {
    --ink: #3a3a3a;
    --ink-soft: #555555;
    --ink-strong: #1e1e1e;
    --rule: #8a8a8a;
    --rule-light: #c9c9c9;
    --frame: #888888;
    --paper: #ffffff;
    --photo-bg: #f2f2f2;
  }
  * { margin: 0; padding: 0; box-sizing: border-box; }
  html, body { width: 1200px; height: 3131px; overflow: hidden; background: var(--paper); }
  body { position: relative; font-family: 'Quicksand', sans-serif; color: var(--ink); }

  .site-header { position: absolute; left: 0; top: 0; width: 1200px; height: 98px; border-bottom: 1px solid var(--rule); }
  .brand { position: absolute; left: 0; width: 1200px; top: 18px; text-align: center; font-size: 43px; font-weight: 400; letter-spacing: 2px; color: var(--ink); }

  .main-nav { position: absolute; left: 0; top: 98px; width: 1200px; height: 60px; }
  .main-nav a { position: absolute; top: 19px; transform: translateX(-50%); font-size: 16px; font-weight: 400; color: var(--ink-strong); text-decoration: none; letter-spacing: .3px; }
  .main-nav a.is-active::after { content: ""; position: absolute; left: 50%; transform: translateX(-50%); top: 26px; width: 45px; height: 2px; background: var(--ink-strong); }

  .hero { position: absolute; left: 0; top: 158px; width: 1200px; height: 658px;
    background:
      radial-gradient(ellipse at 30% 45%, #2f8a3a 0%, transparent 45%),
      radial-gradient(ellipse at 70% 25%, #1d7a78 0%, transparent 40%),
      radial-gradient(ellipse at 85% 75%, #6e5a45 0%, transparent 40%),
      radial-gradient(ellipse at 55% 60%, #e9ecea 0%, transparent 35%),
      linear-gradient(120deg, #a6c990 0%, #4fa44a 35%, #2d7f6c 60%, #b8b0a0 100%); }
  .slider-arrow { position: absolute; }

  .section-title { position: absolute; left: 0; width: 1200px; text-align: center; font-weight: 400; font-size: 52px; color: var(--ink); letter-spacing: 1px; }
  .title-rule { position: absolute; left: 568px; width: 64px; height: 3px; background: var(--ink); }

  .headshot-frame { position: absolute; left: 450px; top: 996px; width: 306px; height: 300px; border: 2px solid var(--frame); padding: 4px; }
  .headshot { width: 100%; height: 100%; background: linear-gradient(180deg, #f4f4f4 0%, #e8e6e4 100%); }

  .bio { position: absolute; left: 140px; width: 932px; top: 1334px; text-align: center; font-size: 18.5px; font-weight: 300; line-height: 27px; color: var(--ink-soft); }
  .bio p + p { margin-top: 15px; }

  .divider { position: absolute; left: 0; width: 1200px; height: 1px; background: var(--rule); }
  .divider-mark { position: absolute; left: 601px; top: -7px; width: 14px; height: 14px; background: var(--paper); border: 2px solid var(--ink); }

  .artwork-backing { position: absolute; left: 178px; top: 1830px; width: 868px; height: 531px; border: 3px solid var(--frame); }
  .artwork { position: absolute; left: 163px; top: 1812px; width: 868px; height: 535px;
    background:
      radial-gradient(ellipse at 70% 35%, #d99b55 0%, transparent 30%),
      radial-gradient(ellipse at 15% 85%, #c48a1a 0%, transparent 28%),
      radial-gradient(ellipse at 50% 60%, #3c7fc6 0%, transparent 35%),
      radial-gradient(ellipse at 20% 15%, #d6b24a 0%, transparent 25%),
      linear-gradient(160deg, #f1ede4 0%, #e7eef3 50%, #efe9de 100%); }

  .contact-intro { position: absolute; left: 0; width: 1200px; top: 2676px; text-align: center; font-size: 19px; font-weight: 300; color: var(--ink-soft); }
  .contact-line { position: absolute; left: 0; width: 1200px; text-align: center; font-size: 20px; font-weight: 400; color: var(--ink-strong); }
  .social { position: absolute; left: 0; width: 1200px; text-align: center; font-size: 21px; font-weight: 400; color: var(--ink); }
  .social .dot { display: inline-block; width: 26px; height: 26px; border: 2px solid var(--ink); border-radius: 50%; vertical-align: -5px; margin-right: 8px; }

  .site-footer { position: absolute; left: 0; top: 3053px; width: 1200px; height: 78px; border-top: 1px solid var(--rule-light); }
  .site-footer p { position: absolute; left: 0; width: 1230px; top: 24px; text-align: center; font-size: 14px; color: var(--ink-soft); }
</style>
</head>
<body>
  <header class="site-header">
    <div class="brand">LORNA VELCOURT</div>
  </header>

  <nav class="main-nav">
    <a class="is-active" href="#home" style="left:270px">HOME</a>
    <a href="#about" style="left:449px">ABOUT ME</a>
    <a href="#gallery" style="left:641px">GALLERY</a>
    <a href="#contact" style="left:828px">CONTACT</a>
  </nav>

  <section class="hero" id="home">
    <div role="img" aria-label="Close-up of an abstract painting in greens, teal and earthy browns" style="position:absolute;inset:0"></div>
    <svg class="slider-arrow" style="left:22px;top:438px" width="30" height="48" viewBox="0 0 30 48"><polyline points="24,4 6,24 24,44" fill="none" stroke="#ffffff" stroke-width="3"/></svg>
    <svg class="slider-arrow" style="left:1136px;top:438px" width="30" height="48" viewBox="0 0 30 48"><polyline points="6,4 24,24 6,44" fill="none" stroke="#ffffff" stroke-width="3"/></svg>
  </section>

  <section id="about">
    <h2 class="section-title" style="top:890px">ABOUT ME</h2>
    <div class="title-rule" style="top:958px"></div>
    <div class="headshot-frame">
      <div class="headshot" role="img" aria-label="Artist headshot"></div>
    </div>
    <div class="bio">
      <p>Lorem ipsum dolor sit amet, consectetur adipiscing elit, sed do eiusmod tempor incididunt ut labore et dolore magna aliqua. Ut enim ad minim veniam, quis nostrud exercitation Lorem ipsum dolor sit amet, consectetur adipiscing elit, sed do eiusmod tempor incididunt ut labore et dolore magna aliqua.</p>
      <p>Duis aute irure dolor in reprehenderit in voluptate velit esse cillum dolore eu fugiat nulla pariatur. Excepteur sint occaecat cupidatat non proident, sunt in culpa qui officia deserunt mollit anim id est laborum.Sed ut perspiciatis unde pariatur. Excepteur sint occaecat cupidatat non proident, sunt in culpa qui officia deserunt mollit anim id est laborum.Sed ut persmollit anim id est laborum.Sed ut perspiciatis unde pariatur. Excepteur sin</p>
    </div>
  </section>

  <div class="divider" style="top:1637px"><span class="divider-mark"></span></div>

  <section id="gallery">
    <h2 class="section-title" style="top:1690px">GALLERY</h2>
    <div class="title-rule" style="top:1757px"></div>
    <div class="artwork-backing"></div>
    <div class="artwork" role="img" aria-label="Abstract painting with blue, ochre and rust brushstrokes on a pale ground"></div>
    <svg class="slider-arrow" style="left:86px;top:2044px" width="28" height="48" viewBox="0 0 28 48"><polyline points="23,3 5,24 23,45" fill="none" stroke="#444444" stroke-width="3.5"/></svg>
    <svg class="slider-arrow" style="left:1084px;top:2044px" width="28" height="48" viewBox="0 0 28 48"><polyline points="5,3 23,24 5,45" fill="none" stroke="#444444" stroke-width="3.5"/></svg>
  </section>

  <div class="divider" style="top:2489px"><span class="divider-mark"></span></div>

  <section id="contact">
    <h2 class="section-title" style="top:2580px">CONTACT US</h2>
    <div class="title-rule" style="top:2648px;left:584px"></div>
    <p class="contact-intro">Please get in touch with me on below details.</p>
    <p class="contact-line" style="top:2744px">Email : info@lornavelcourt.com</p>
    <p class="contact-line" style="top:2793px">Phone: (123) 555 0147</p>
    <p class="social" style="top:2845px"><span class="dot"></span>@lvelcourtart</p>
    <p class="social" style="top:2901px"><span class="dot"></span>@lvpainter</p>
  </section>

  <footer class="site-footer">
    <p>© 2022 Lorna Velcourt &nbsp; All Rights Reserved</p>
  </footer>
</body>
</html>
```